New letter head for Air Conditioning business

We need a new professional letter head design to suit our new re-branded air conditioning business. Our new logo is attached

```html
<!DOCTYPE html>
<html lang="en">
<head>
<meta charset="utf-8">
<title>Coolwave Letterhead</title>
<link href="https://fonts.googleapis.com/css2?family=Questrial&display=swap" rel="stylesheet">
<style>
  :root {
    --paper: #f0f0f0;
    --ink: #34343a;
    --text: #3a3a3a;
    --green: #5bb07a;
    --red: #de5a50;
  }
  * { margin: 0; padding: 0; box-sizing: border-box; }
  html, body { width: 971px; height: 1200px; overflow: hidden; background: var(--paper); }
  body { font-family: "Questrial", "Century Gothic", sans-serif; color: var(--text); }
  .letterhead { position: relative; width: 971px; height: 1200px; background: var(--paper); }

  .brand { position: absolute; left: 53px; top: 52px; display: flex; align-items: center; gap: 18px; }
  .brand-dot { width: 58px; height: 58px; border-radius: 50%; background: var(--green); }
  .brand-name { font-size: 40px; letter-spacing: 4px; color: var(--ink); line-height: 1; }

  .address { position: absolute; right: 311px; top: 51px; text-align: right; font-size: 15px; line-height: 17.6px; color: var(--ink); }
  .divider { position: absolute; left: 678px; top: 51px; width: 2px; height: 62px; background: var(--red); }
  .contacts { position: absolute; left: 699px; top: 45px; list-style: none; font-size: 15px; line-height: 17.6px; color: var(--ink); }
  .contacts li { display: flex; align-items: center; gap: 7px; }
  .contacts svg { width: 11px; height: 11px; fill: var(--green); flex: none; }

  .recipient { position: absolute; left: 53px; top: 280px; font-size: 15px; line-height: 24.5px; }
  .body-copy { position: absolute; left: 53px; width: 861px; top: 393px; font-size: 15px; line-height: 24.3px; text-align: justify; }
  .body-copy p + p { margin-top: 21px; }
  .closing { position: absolute; left: 53px; top: 800px; font-size: 15px; }
  .signature { position: absolute; left: 53px; top: 838px; width: 178px; height: 64px; background: linear-gradient(90deg, #e4e4e4, #ececec); }

  .mark-faint { position: absolute; right: 55px; top: 995px; width: 190px; height: 190px; border-radius: 50%; background: var(--green); opacity: 0.06; }

  .footer-band { position: absolute; left: 0; bottom: 0; width: 971px; height: 12px; }
</style>
</head>
<body>
<main class="letterhead">
  <header>
    <div class="brand">
      <span class="brand-dot"></span>
      <span class="brand-name">COOLWAVE</span>
    </div>
    <address class="address">1840 Harbor View Road,<br>Suite 214 Lakeside,<br>CA 90210</address>
    <span class="divider"></span>
    <ul class="contacts">
      <li><svg viewBox="0 0 12 12"><path d="M2.5 1l2 2.2-1 1.3c.7 1.4 1.8 2.5 3.2 3.2l1.3-1 2.2 2-1.2 2C5 10.5 1.5 7 1 2.2z"/></svg>555-014-2286</li>
      <li><svg viewBox="0 0 12 12"><path d="M3 1h6v3H3zM1 5h10v4H9v2H3V9H1zM4 8v2h4V8z"/></svg>555-018-7730</li>
      <li><svg viewBox="0 0 12 12"><path d="M1 3h10v6H1zm1 1v.3L6 7l4-2.7V4L6 6.5z"/></svg>info@coolwaveair.com</li>
      <li><svg viewBox="0 0 12 12"><circle cx="6" cy="6" r="5"/></svg>www.coolwaveair.com</li>
    </ul>
  </header>

  <section class="recipient">
    <p>Mr/s</p>
    <p>First Name and Last Name</p>
    <p>Company Name</p>
    <p>Address</p>
  </section>

  <section class="body-copy">
    <p>Lorem Ipsum is simply dummy text of the printing and typesetting industry. Lorem Ipsum has been the industry's standard dummy text ever since the 1500s, when an unknown printer took a galley of type and scrambled it to make a type specimen book. It has survived not only five centuries, but also the leap into electronic typesetting, remaining essentially unchanged. It was popularised in the 1960s with the release of Letraset sheets containing Lorem Ipsum passages.</p>
    <p>he standard chunk of Lorem Ipsum used since the 1500s is reproduced below for those interested. Sections 1.10.32 and 1.10.33 from "de Finibus Bonorum et Malorum" by Cicero are also reproduced in their exact original form, accompanied by English versions from the 1914 translation by H. Rackham. Lorem ipsum dolor sit amet, consectetur adipiscing elit, sed do eiusmod tempor incididunt ut labore et dolore magna aliqua.</p>
    <p>It is a long established fact that a reader will be distracted by the readable content of a page when looking at its layout. The point of using Lorem Ipsum is that it has a more-or-less normal distribution of letters, as opposed to using 'Content here, content here', making it look like readable English. Many desktop publishing packages and web page editors now .</p>
  </section>

  <p class="closing">Your Sincerely,</p>
  <div class="signature" role="img" aria-label="Handwritten signature"></div>

  <span class="mark-faint"></span>

  <svg class="footer-band" viewBox="0 0 971 12" preserveAspectRatio="none">
    <polygon points="0,0 481,0 469,12 0,12" fill="var(--green)"/>
    <polygon points="489,0 971,0 971,12 477,12" fill="var(--red)"/>
  </svg>
</main>
</body>
</html>
```